Bespoke catering company needs a simple but effective kick ass website

I need a website for a bespoke catering company based in the west side of Melbourne called "plato" by Marcus Hendley, I used the words Feast-Table-Occasions on my business cards which i still want to maintain through out the site.
My main market is aimed towards, in-house dining experiences of restaurant quality, cocktail food, small weddings / engagements, small events.
I have a plato logo in yellow in Hoefler title font with a black background, so the website design would include yellow and black and still using the Hoefler Titling font.
I want the site map to have 5 drop down bars including Home, About Me, Gallery, Menu, Contact me. It needs to be easy to move around.
I want links to my Facebook page, instagram and twitter.
The site needs to be easy for myself to change on a regular basis due to changing seasonal menus and gallery pictures.
Updates
Hi,
I have just added loads of photos of my food into the brief and adjusted the preferences slightly. Can you please update your submissions using my photos?
Thanks,
Marcus
Target Market(s)
The target market is customers looking for quality ,restaurant style dining and cocktail food in their own home or for their private event.
Industry/Entity Type
Restaurant
Font styles to use
Other font styles liked:
- Hoefler Titling
Look and feel
Each slider illustrates characteristics of the customer's brand and the style your logo design should communicate.

```html
<!DOCTYPE html>
<html lang="en">
<head>
<meta charset="utf-8">
<title>plato — by Marcus Hendley</title>
<link rel="stylesheet" href="https://fonts.googleapis.com/css2?family=Open+Sans:wght@400;600&family=Roboto+Slab:wght@400;500&display=swap">
<style>
:root{
  --ink:#231f20;
  --page:#f1ebcf;
  --white:#ffffff;
  --gold:#f0c419;
  --gold-deep:#d9a90c;
  --olive:#9a8a1f;
  --text:#555555;
  --dark-text:#2b2b2b;
  --red:#a3282b;
  --panel:#eeeeee;
  --rule:#c9c9c9;
  --icon-light:#d8d8d8;
  --icon-dark:#3a3a3a;
}
*{margin:0;padding:0;box-sizing:border-box}
html,body{width:890px;height:1200px;overflow:hidden}
body{position:relative;background:var(--page);font-family:"Open Sans",Arial,sans-serif;color:var(--text)}
h1,h2,h3{font-weight:400}
.abs{position:absolute}

/* header */
.site-header{left:0;top:0;width:890px;height:109px;background:var(--ink)}
.brand{left:74px;top:8px;font-family:"Roboto Slab",Georgia,serif;font-size:58px;font-weight:400;color:var(--white);letter-spacing:-1px;line-height:1}
.brand-by{left:150px;top:76px;font-family:"Roboto Slab",Georgia,serif;font-size:10px;color:var(--gold)}
.social{display:flex;gap:7px}
.social span{display:block;border-radius:50%;position:relative}
.social span::after{content:"";position:absolute;left:5px;top:5px;right:5px;bottom:5px;border-radius:50%;border:2px solid var(--ink)}
.social--top{left:582px;top:23px}
.social--top span{width:22px;height:22px;background:var(--icon-light)}
.social--top span:first-child{background:var(--gold)}
.search{left:675px;top:23px;width:141px;height:22px;background:var(--white);font-size:10px;color:#888;padding:4px 10px}
.search svg{position:absolute;right:6px;top:4px}
.main-nav{left:530px;top:74px;font-size:11.5px;color:var(--white);white-space:nowrap}
.main-nav a{color:var(--white);text-decoration:none}
.main-nav a.active{color:var(--gold)}
.main-nav .sep{color:#8a8a8a;margin:0 8px}

/* slider */
.slider{left:74px;top:125px;width:743px;height:362px;background:var(--white);padding:4px;box-shadow:0 0 3px rgba(0,0,0,.2)}
.slider-photo{width:100%;height:100%;
  background:
    radial-gradient(ellipse 9% 6% at 57% 6%, rgba(255,250,235,.95), rgba(255,250,235,0)),
    radial-gradient(ellipse 7% 5% at 90% 16%, rgba(255,250,235,.9), rgba(255,250,235,0)),
    radial-gradient(ellipse 10% 14% at 12% 45%, rgba(255,150,60,.8), rgba(255,150,60,0)),
    radial-gradient(ellipse 14% 30% at 34% 30%, rgba(110,140,90,.55), rgba(110,140,90,0)),
    radial-gradient(ellipse 12% 25% at 95% 30%, rgba(110,150,100,.55), rgba(110,150,100,0)),
    radial-gradient(ellipse 32% 24% at 55% 70%, rgba(240,228,200,.75), rgba(240,228,200,0)),
    linear-gradient(180deg,#d8b47a 0%,#c09258 35%,#8a5d33 68%,#4a2b18 100%);}
.slider-caption{left:4px;bottom:4px;width:735px;height:50px;background:rgba(30,28,26,.85);color:var(--white);font-size:19px;padding:12px 22px}
.slider-arrows{right:22px;top:17px;display:flex;gap:2px}
.slider-arrows span{width:15px;height:15px;background:#f2f2f2;display:flex;align-items:center;justify-content:center}

/* call to action */
.cta-title{left:140px;top:503px;font-family:"Roboto Slab",Georgia,serif;font-size:21px;color:var(--dark-text)}
.cta-contact{left:141px;top:534px;font-size:11.5px;color:var(--dark-text);display:flex;align-items:center;gap:5px}
.cta-contact .sep{margin:0 8px}
.book-btn{left:583px;top:508px;width:167px;height:40px;background:linear-gradient(#4a4a4a,#2e2e2e);border-radius:3px;color:var(--white);font-size:13px;font-weight:600;display:flex;align-items:center;justify-content:center;box-shadow:0 1px 2px rgba(0,0,0,.4)}

/* content panel */
.content{left:74px;top:571px;width:743px;height:533px;background:var(--white)}
.welcome-title{left:86px;top:582px;font-family:"Roboto Slab",Georgia,serif;font-size:22px;color:var(--olive)}
.welcome-text{left:87px;top:621px;width:510px;font-size:10.3px;line-height:17px}
.rule{height:0;border-top:1px dotted var(--rule)}
.gallery-title{left:86px;top:709px;font-family:"Roboto Slab",Georgia,serif;font-size:14.5px;color:var(--olive)}
.mini-arrows{left:569px;top:713px;display:flex;gap:2px}
.mini-arrows span{width:12px;height:12px;border-radius:50%;background:#e4e4e4;display:flex;align-items:center;justify-content:center}
.product{top:745px;width:158px;text-align:center}
.product-photo{width:158px;height:106px;box-shadow:0 1px 2px rgba(0,0,0,.3)}
.product-name{margin-top:9px;font-size:11px;color:var(--dark-text)}
.product-date{margin-top:2px;font-size:9px;color:var(--text)}

/* sidebar */
.ribbon{left:621px;top:594px;width:184px;height:36px}
.ribbon-label{left:621px;top:594px;width:184px;height:34px;display:flex;align-items:center;justify-content:center;font-family:"Roboto Slab",Georgia,serif;font-size:13.5px;font-weight:500;color:#5a4a10}
.daily-menu{left:622px;top:640px;width:183px;list-style:none}
.daily-menu li{height:29.4px;border-bottom:1px dotted var(--rule);display:flex;align-items:center;font-size:12px;color:var(--red);padding-left:6px}
.daily-menu li svg{margin-right:10px}

/* about */
.about{left:86px;top:939px;width:719px;height:146px;background:var(--panel);border:1px solid #dddddd}
.about-photo{left:0;top:0;width:221px;height:144px;
  background:
    radial-gradient(ellipse 30% 55% at 50% 62%, rgba(250,250,248,.95), rgba(250,250,248,0)),
    radial-gradient(ellipse 40% 25% at 85% 85%, rgba(235,220,190,.8), rgba(235,220,190,0)),
    radial-gradient(ellipse 30% 20% at 20% 15%, rgba(230,170,90,.7), rgba(230,170,90,0)),
    linear-gradient(180deg,#5e4630 0%,#3f3025 55%,#2c241e 100%);}
.about-title{left:243px;top:22px;font-family:"Roboto Slab",Georgia,serif;font-size:14.5px;color:var(--dark-text)}
.about-text{left:243px;top:51px;width:460px;font-size:10.3px;line-height:17px}
.about-text a{color:var(--red);text-decoration:none;margin-left:3px}

/* footer */
.footer-nav{left:75px;top:1130px;font-size:10.5px;color:var(--dark-text)}
.footer-nav .sep{margin:0 7px}
.copyright{left:75px;top:1155px;font-size:10.5px;color:var(--dark-text)}
.social--foot{left:737px;top:1140px}
.social--foot span{width:22px;height:22px;background:var(--icon-dark)}
.social--foot span::after{border-color:var(--page)}
</style>
</head>
<body>

<header class="site-header abs"></header>
<div class="brand abs">plato</div>
<div class="brand-by abs">by marcus hendley</div>

<div class="social social--top abs" aria-label="Social links"><span></span><span></span><span></span></div>
<div class="search abs">Search
  <svg width="12" height="12" viewBox="0 0 12 12"><circle cx="4.5" cy="4.5" r="3.2" fill="none" stroke="#222" stroke-width="1.6"/><line x1="7" y1="7" x2="11" y2="11" stroke="#222" stroke-width="2"/></svg>
</div>
<nav class="main-nav abs">
  <a class="active" href="#">Home</a><span class="sep">/</span><a href="#">About Me</a><span class="sep">/</span><a href="#">Gallery</a><span class="sep">/</span><a href="#">Menu</a><span class="sep">/</span><a href="#">Contact me</a>
</nav>

<section class="slider abs">
  <div class="slider-photo" role="img" aria-label="Elegant dining room with a glass table, cream chairs, pendant lights and a fireplace"></div>
  <div class="slider-caption abs">Etiam sit amet aliquam nunc, quis luctus dui
    <div class="slider-arrows abs">
      <span><svg width="6" height="9" viewBox="0 0 6 9"><path d="M5 1 1 4.5 5 8" fill="none" stroke="#333" stroke-width="1.4"/></svg></span>
      <span><svg width="6" height="9" viewBox="0 0 6 9"><path d="M1 1 5 4.5 1 8" fill="none" stroke="#333" stroke-width="1.4"/></svg></span>
    </div>
  </div>
</section>

<h2 class="cta-title abs">Quisque enim nisl, semper sit amet lectus nec</h2>
<div class="cta-contact abs">
  <svg width="13" height="11" viewBox="0 0 13 11"><path d="M2 1c1 0 2 2 2 3L3 5c1 2 2 3 4 4l1-1c1 0 3 1 3 2l-1 1C6 11 1 6 1 2z" fill="#333"/></svg>
  <span>Call Me Today : &nbsp;0400 555 018</span><span class="sep">/</span>
  <svg width="12" height="10" viewBox="0 0 12 10"><rect x="1" y="2" width="10" height="7" fill="none" stroke="#333"/><path d="M1 2 6 6 11 2" fill="none" stroke="#333"/></svg>
  <span>E-mail : &nbsp;info@platofeasts.com</span>
</div>
<div class="book-btn abs">BOOK AN EVENT NOW</div>

<main class="content abs"></main>

<h1 class="welcome-title abs">Welcome to Plato</h1>
<p class="welcome-text abs">Donec at gravida quam, ut rhoncus nisl. Nulla facilisi. Vivamus et sollicitudin quam. Sed in massa venenatis, molestie ante sed, aliquam tortor. Suspendisse a dolor lacinia, venenatis purus et, ultricies orci. Nam iaculis rutrum sem, et suscipit ipsum vestibulum ut. Cras enim neque, volutpat non varius vel.</p>
<div class="rule abs" style="left:85px;top:687px;width:510px"></div>

<h3 class="gallery-title abs">Product Gallery</h3>
<div class="mini-arrows abs">
  <span><svg width="4" height="6" viewBox="0 0 4 6"><path d="M3 1 1 3 3 5" fill="none" stroke="#666"/></svg></span>
  <span><svg width="4" height="6" viewBox="0 0 4 6"><path d="M1 1 3 3 1 5" fill="none" stroke="#666"/></svg></span>
</div>

<article class="product abs" style="left:86px">
  <div class="product-photo" role="img" aria-label="Outdoor catered event with a grill and a white set table" style="background:radial-gradient(ellipse 45% 30% at 60% 45%,rgba(255,255,255,.95),rgba(255,255,255,0)),radial-gradient(ellipse 40% 18% at 65% 88%,rgba(120,150,60,.7),rgba(120,150,60,0)),linear-gradient(180deg,#c8ccc8 0%,#e6e6e2 45%,#6a625a 80%,#2e2a26 100%)"></div>
  <div class="product-name">Maecenas consequat tortor</div>
  <div class="product-date">December 27, 2013</div>
</article>
<article class="product abs" style="left:262px">
  <div class="product-photo" role="img" aria-label="Festive table with roast dishes, white plates and a red tablecloth" style="background:radial-gradient(ellipse 30% 18% at 35% 65%,rgba(250,245,240,.95),rgba(250,245,240,0)),radial-gradient(ellipse 40% 30% at 55% 25%,rgba(215,150,60,.9),rgba(215,150,60,0)),linear-gradient(180deg,#a86a2a 0%,#c98a3c 40%,#c0312e 70%,#8c1c1e 100%)"></div>
  <div class="product-name">Maecenas consequat tortor</div>
  <div class="product-date">December 27, 2013</div>
</article>
<article class="product abs" style="left:437px">
  <div class="product-photo" role="img" aria-label="Overhead view of shared dishes on a wooden table" style="background:radial-gradient(ellipse 22% 22% at 45% 10%,rgba(140,30,45,.85),rgba(140,30,45,0)),radial-gradient(ellipse 25% 30% at 25% 70%,rgba(240,230,210,.9),rgba(240,230,210,0)),radial-gradient(ellipse 25% 25% at 62% 50%,rgba(200,150,60,.9),rgba(200,150,60,0)),radial-gradient(ellipse 18% 30% at 92% 60%,rgba(70,120,50,.8),rgba(70,120,50,0)),linear-gradient(135deg,#6e4426,#9a6a3c 50%,#5a3820)"></div>
  <div class="product-name">Maecenas consequat tortor</div>
  <div class="product-date">December 27, 2013</div>
</article>
<div class="rule abs" style="left:85px;top:910px;width:510px"></div>

<svg class="ribbon abs" viewBox="0 0 184 36" aria-hidden="true">
  <path d="M6 0H178L184 8V28L178 34H6L0 28V8Z" fill="var(--gold)"/>
  <path d="M0 28 6 34 6 36 0 30Z" fill="var(--gold-deep)"/>
  <path d="M184 28 178 34 178 36 184 30Z" fill="var(--gold-deep)"/>
</svg>
<div class="ribbon-label abs">MENU OF THE DAY</div>
<ul class="daily-menu abs">
  <li><svg width="9" height="8" viewBox="0 0 9 8"><path d="M1 0V7H9" fill="none" stroke="#bbb" stroke-dasharray="1 1"/></svg>Etiam id pulvinar</li>
  <li><svg width="9" height="8" viewBox="0 0 9 8"><path d="M1 0V7H9" fill="none" stroke="#bbb" stroke-dasharray="1 1"/></svg>Donec feugiat turpis</li>
  <li><svg width="9" height="8" viewBox="0 0 9 8"><path d="M1 0V7H9" fill="none" stroke="#bbb" stroke-dasharray="1 1"/></svg>Nam iaculis rutrum</li>
  <li><svg width="9" height="8" viewBox="0 0 9 8"><path d="M1 0V7H9" fill="none" stroke="#bbb" stroke-dasharray="1 1"/></svg>Morbi tempus velitarcu</li>
  <li><svg width="9" height="8" viewBox="0 0 9 8"><path d="M1 0V7H9" fill="none" stroke="#bbb" stroke-dasharray="1 1"/></svg>Praesent cursus</li>
  <li><svg width="9" height="8" viewBox="0 0 9 8"><path d="M1 0V7H9" fill="none" stroke="#bbb" stroke-dasharray="1 1"/></svg>Mauris tincidunt</li>
  <li><svg width="9" height="8" viewBox="0 0 9 8"><path d="M1 0V7H9" fill="none" stroke="#bbb" stroke-dasharray="1 1"/></svg>Nulla feugiat laciniased</li>
  <li><svg width="9" height="8" viewBox="0 0 9 8"><path d="M1 0V7H9" fill="none" stroke="#bbb" stroke-dasharray="1 1"/></svg>Nulla lacus</li>
  <li><svg width="9" height="8" viewBox="0 0 9 8"><path d="M1 0V7H9" fill="none" stroke="#bbb" stroke-dasharray="1 1"/></svg>Sed vitae venenatis</li>
</ul>

<section class="about abs">
  <div class="about-photo abs" role="img" aria-label="Chef in white uniform standing in a restaurant kitchen"></div>
  <h3 class="about-title abs">About Me</h3>
  <p class="about-text abs">Donec at gravida quam, ut rhoncus nisl. Nulla facilisi. Vivamus et sollicitudin quam. Sed in massa venenatis, molestie ante sed, aliquam tortor. Suspendisse a dolor lacinia, venenatis purus et, ultricies orci. Nam iaculis rutrum sem, et suscipit ipsum vestibulum ut. Cras enim neque, volutpat non varius vel. <a href="#">More</a></p>
</section>

<footer>
  <div class="footer-nav abs">Home<span class="sep">|</span>About Me<span class="sep">|</span>Gallery<span class="sep">|</span>Menu<span class="sep">|</span>Contact me</div>
  <div class="copyright abs">Copyright &nbsp;© &nbsp;2103 &nbsp; Plato. &nbsp;Al lrights reserved</div>
  <div class="social social--foot abs" aria-label="Social links"><span></span><span></span><span></span></div>
</footer>

</body>
</html>
```